New Company Business Card design

Looking for a corporate looking business card utilising my new logo design - the logo i would like embossed as one option and flat as another - simplistic but stylish - less is more - we are an import export business launching into the market - i would like a couple of options as main background - Grey or Black

```html
<!DOCTYPE html>
<html lang="en">
<head>
<meta charset="utf-8">
<title>Meridian Trade Partners – Business Card</title>
<link rel="stylesheet" href="https://fonts.googleapis.com/css2?family=Roboto:wght@400;500;700&display=swap">
<style>
  :root {
    --backdrop: #e8e5e0;
    --card-white: #f4f4f4;
    --brand-blue: #0e74bb;
    --rule-grey: #5f6064;
    --back-grey: #6b6c70;
    --ink-white: #ffffff;
  }
  * { margin: 0; padding: 0; box-sizing: border-box; }
  html, body { width: 1200px; height: 960px; overflow: hidden; }
  body {
    background: var(--backdrop);
    font-family: "Roboto", Arial, sans-serif;
    position: relative;
  }
  .card {
    position: absolute;
    width: 600px;
    height: 343px;
    box-shadow: 0 3px 8px rgba(0,0,0,0.25);
  }
  /* Front */
  .card-front { left: 314px; top: 113px; background: var(--card-white); }
  .front-brand {
    position: absolute; left: 0; top: 0; width: 100%; height: 177px;
    display: flex; align-items: center; justify-content: center;
  }
  .brand-name {
    font-family: "Roboto", Arial, sans-serif;
    font-weight: 500;
    font-size: 28px;
    letter-spacing: 1px;
    color: var(--brand-blue);
  }
  .rule { position: absolute; left: 0; width: 100%; background: var(--rule-grey); }
  .rule-top { top: 177px; height: 4px; }
  .rule-bottom { top: 321px; height: 4px; }
  .contact-band {
    position: absolute; left: 0; top: 182px; width: 100%; height: 137px;
    background: var(--brand-blue); color: var(--ink-white);
  }
  .person { position: absolute; left: 35px; top: 31px; }
  .person-name { font-size: 21px; font-weight: 700; line-height: 24px; letter-spacing: 0.3px; }
  .person-title { font-size: 15px; font-weight: 500; line-height: 19px; margin-bottom: 2px; }
  .person-address { font-size: 14.5px; line-height: 18.5px; font-weight: 400; }
  .contacts {
    position: absolute; right: 33px; top: 38px;
    list-style: none; text-align: right; font-size: 14.5px; line-height: 19.3px;
  }
  .contacts li { display: flex; justify-content: flex-end; align-items: center; gap: 4px; }
  .contacts svg { width: 14px; height: 14px; fill: var(--ink-white); flex: none; }
  /* Back */
  .card-back {
    left: 311px; top: 472px; background: var(--back-grey); color: var(--ink-white);
  }
  .back-name {
    position: absolute; left: 0; top: 125px; width: 100%; text-align: center;
    font-weight: 500; font-size: 42px; letter-spacing: 1px;
  }
  .back-web {
    position: absolute; left: 0; top: 288px; width: 100%; text-align: center;
    font-size: 14px; letter-spacing: 1.6px;
  }
</style>
</head>
<body>
  <section class="card card-front">
    <div class="front-brand"><span class="brand-name">Meridian Trade Partners</span></div>
    <div class="rule rule-top"></div>
    <div class="contact-band">
      <div class="person">
        <p class="person-name">DANIEL REYES</p>
        <p class="person-title">CEO/FOUNDER</p>
        <p class="person-address">1240 Harbor View Road<br>Juneau, Alaska 99801</p>
      </div>
      <ul class="contacts">
        <li>555 214 7730
          <svg viewBox="0 0 16 16" aria-hidden="true"><path d="M3.6 1.2l2.3 2.6-1.2 1.8c.9 2 2.6 3.8 4.7 4.8l1.8-1.2 2.6 2.3-1.3 2.3C7.7 15.6.4 8.3.9 2.5z"/></svg></li>
        <li>555 382 1046
          <svg viewBox="0 0 16 16" aria-hidden="true"><path d="M4.5 0h7a1 1 0 0 1 1 1v14a1 1 0 0 1-1 1h-7a1 1 0 0 1-1-1V1a1 1 0 0 1 1-1zm.6 2v10.5h5.8V2zM8 13.3a.9.9 0 1 0 0 1.8.9.9 0 0 0 0-1.8z"/></svg></li>
        <li>555 617 2289
          <svg viewBox="0 0 16 16" aria-hidden="true"><path d="M4 1h8v3.5H4zM1 5.5h14v6.5h-2.5v-2h-9v2H1zM4.5 11h7v4h-7z"/></svg></li>
        <li>hello@meridiantp.com
          <svg viewBox="0 0 16 16" aria-hidden="true"><path d="M1 3.5h14v.6L8 8.6 1 4.1zM1 5.6l7 4.5 7-4.5v7H1z"/></svg></li>
      </ul>
    </div>
    <div class="rule rule-bottom"></div>
  </section>

  <section class="card card-back">
    <p class="back-name">Meridian Trade Partners</p>
    <p class="back-web">www.meridiantradepartners.com</p>
  </section>
</body>
</html>
```